velorimo.gr wordpress makeover

We need a makeover of our wordpress website velorimo.gr We are a company that provides astrology services via phone either by billable phone number or by prepaid packages.This is what we sell. Moreover, we share everyday astrology related articles to our blog. It will be a multy page website. Our goal is always to sell our phone prepaid packages or to make the visitor of the website call our billable numbers. Our website should have:
-a home page introducing its content (astrologers, call packages, blog section with categories).
-astrologers page (you can see the existing one to understand)
-Phone packages page (eshop page where you can buy prepaid phone packages. woo commerce maybe)
- Blog page divined by categories.
The website should have places for display banners eg. a sidebar.
I will provide some screen shots of websites we like. You can always visit our existing website www.velorimo.gr to see it for yourself.

Target Market(s)

people seeking for future telling - astrologer services via phone. People who like to be informed about everyday astrology predictions

Industry/Entity Type

Astrology - tarot services via phone

Coding

Coded - Design and coding required

Number of Pages Required

5+ page

Font styles to use
Decorative
Script

Colors
6B429C
8869AF
B7A5CE
E3DAEB
F3F0F8

Requirements
Must have
• -Home page -Astrologers page -Phone packages page (eshop) -Blog page with categories - Made following the guidelines of quenbly so as to be efficient in quenbly ads marketing. Mobile friendly.
Nice to have
• Nice call to action buttons to call or buy packages. Sidebar with banner ads of maybe our offers.

```html
<!DOCTYPE html>
<html lang="el">
<head>
<meta charset="utf-8">
<title>velorimo.gr</title>
<link rel="stylesheet" href="https://fonts.googleapis.com/css2?family=Roboto:ital,wght@0,300;0,400;0,500;0,700;1,400&display=swap">
<style>
:root{
  --purple:#6B429C;
  --purple-mid:#8869AF;
  --purple-soft:#B7A5CE;
  --lilac:#E3DAEB;
  --lilac-pale:#F3F0F8;
  --ink:#2b2b2b;
  --muted:#6f6f6f;
  --night:#1a1a22;
  --white:#fff;
}
*{margin:0;padding:0;box-sizing:border-box}
html,body{width:1200px;height:4087px;overflow:hidden}
body{font-family:"Roboto",Arial,sans-serif;color:var(--ink);background:var(--white);position:relative}
.abs{position:absolute}

/* Hero */
.hero{position:absolute;left:0;top:0;width:1200px;height:719px;overflow:hidden;
  background:radial-gradient(ellipse at 75% 45%,#c04aa8 0%,#5b3fa8 25%,#27236b 50%,#121435 80%),#121435}
.hero::after{content:"";position:absolute;left:0;right:0;bottom:0;height:260px;
  background:linear-gradient(180deg,rgba(60,70,140,0) 0%,rgba(120,130,190,.55) 60%,rgba(80,90,150,.7) 100%)}
.brand{position:absolute;display:flex;align-items:center;gap:6px;font-family:"Roboto",sans-serif;font-weight:400;color:var(--white)}
.brand .dot{width:22px;height:22px;border-radius:50%;background:var(--white)}
.hero .brand{left:111px;top:40px;font-size:42px;z-index:2}
.main-nav{position:absolute;top:58px;right:111px;display:flex;gap:58px;z-index:2}
.main-nav a{color:var(--white);text-decoration:none;font-size:16px}
.hero-title{position:absolute;left:111px;top:214px;width:520px;color:var(--white);font-size:48px;font-weight:500;line-height:62px;z-index:2}
.hero-text{position:absolute;left:111px;top:362px;width:460px;color:var(--white);font-size:18px;line-height:33px;z-index:2}
.call-btn{position:absolute;left:111px;top:484px;width:194px;height:63px;border:2px solid var(--white);border-radius:32px;background:var(--purple);display:flex;align-items:center;gap:18px;padding-left:6px;color:var(--white);font-size:26px;z-index:2}
.call-btn .ico{width:50px;height:50px;border-radius:50%;background:var(--white);display:flex;align-items:center;justify-content:center}
.wheel{position:absolute;left:579px;top:135px;width:508px;height:508px;border-radius:50%;z-index:1;
  background:radial-gradient(circle,#ffe9b8 0%,#f6a14a 14%,#b64aa8 38%,#4b5ec8 70%,#3aa3e0 100%);opacity:.85}
.thumbs{position:absolute;left:1107px;top:247px;z-index:2}
.thumbs span{display:block;width:72px;height:72px;border-radius:50%;border:3px solid var(--white);margin-bottom:14px}
.thumbs span:nth-child(1){border-color:#63d34a;background:radial-gradient(circle,#f6a14a,#7a3ab4)}
.thumbs span:nth-child(2){background:linear-gradient(135deg,#b9e3f2,#3b8fc4)}
.thumbs span:nth-child(3){background:linear-gradient(135deg,#3a4a7a,#8fa3c9)}
.dots{position:absolute;left:576px;top:688px;display:flex;gap:6px;z-index:2}
.dots i{width:12px;height:12px;border-radius:50%;background:var(--white)}
.dots i+i{background:#222}

/* Filters */
.filters{position:absolute;left:111px;top:778px;display:flex;gap:9px}
.filters span{width:156px;height:46px;border:1px solid #cfcfcf;border-radius:3px;font-size:13px;display:flex;align-items:center;justify-content:center}
.filters span.on{background:var(--purple);border-color:var(--purple);color:var(--white)}

.section-title{position:absolute;font-size:33px;font-weight:400;color:#333}
.section-title::after{content:"";position:absolute;left:0;top:52px;width:56px;height:3px;background:var(--purple)}
.section-title.center::after{left:50%;margin-left:-28px}

/* Blog grid */
.post{position:absolute;width:314px}
.post .img{height:237px}
.post .meta{margin-top:24px;font-size:18px;color:var(--purple)}
.post h3{margin-top:10px;font-size:19px;font-weight:500;line-height:30px}

.recent{position:absolute;left:786px;top:946px;width:303px}
.recent li{list-style:none;display:flex;gap:17px;height:116px}
.recent .img{width:103px;height:90px;flex:none}
.recent h4{font-size:15px;font-weight:400;line-height:23px;margin-top:0}
.recent .time{font-size:14px;color:var(--purple);margin-top:4px;display:flex;align-items:center;gap:4px}

/* Astrologers */
.astro{position:absolute;left:0;top:1706px;width:1200px;height:1262px;background:var(--purple)}
.astro .section-title{color:var(--white);width:1200px;text-align:center;top:42px}
.astro .section-title::after{background:var(--white)}
.card{position:absolute;width:314px;height:487px;background:var(--lilac-pale)}
.card .img{height:235px}
.card .band{height:63px;background:var(--purple-mid);display:flex;align-items:center;padding-left:12px;color:var(--white)}
.card .band .ico{width:42px;height:42px;border-radius:50%;background:var(--purple);display:flex;align-items:center;justify-content:center;flex:none}
.card .num{margin-left:7px;line-height:1}
.card .num small{display:block;font-size:13px}
.card .num b{font-size:29px;font-weight:500}
.card .name{border-left:1px solid rgba(255,255,255,.6);margin-left:18px;padding-left:18px;font-size:20px;height:36px;display:flex;align-items:center}
.card p{padding:22px 20px;font-size:14px;line-height:26px;color:var(--muted);text-align:justify}
.outline-btn{position:absolute;width:182px;height:57px;border:1.5px solid var(--white);border-radius:29px;color:var(--white);font-size:17px;display:flex;align-items:center;justify-content:center}

/* Packages */
.pack{position:absolute;text-align:center;background:var(--white);box-shadow:0 0 14px rgba(0,0,0,.1);border-radius:8px}
.pack .label{font-size:40px;font-weight:300;color:#555}
.pack .price{font-size:72px;font-weight:700;color:var(--purple);margin-top:6px}
.pack hr{border:0;height:1px;background:linear-gradient(90deg,transparent,#bbb,transparent);margin:18px 22px 0}
.pack p{font-size:15px;line-height:29px;color:var(--muted);padding:26px 26px 0}
.pack.featured{background:var(--purple);z-index:2;border-radius:6px}
.pack.featured .label,.pack.featured .price,.pack.featured p{color:var(--white)}
.pack.featured hr{background:linear-gradient(90deg,transparent,rgba(255,255,255,.8),transparent)}
.solid-btn{position:absolute;width:182px;height:57px;border-radius:29px;background:var(--purple);color:var(--white);font-size:17px;display:flex;align-items:center;justify-content:center}

/* Footer */
.site-footer{position:absolute;left:0;top:3742px;width:1200px;height:345px;background:radial-gradient(ellipse at 60% 40%,#2a2a44,var(--night) 70%)}
.site-footer .brand{left:0;width:1200px;justify-content:center;top:60px;font-size:44px}
.foot-nav{position:absolute;top:146px;width:1200px;display:flex;justify-content:center;gap:30px;color:var(--white);font-size:17px}
.social{position:absolute;top:212px;left:496px;display:flex;gap:7px}
.social i{width:36px;height:36px;border-radius:50%;border:1.5px solid var(--white)}
.copy{position:absolute;top:274px;width:1200px;text-align:center;color:var(--white);font-size:15px}
</style>
</head>
<body>

<header class="hero">
  <div class="brand">velorimo<span class="dot"></span></div>
  <nav class="main-nav"><a>Ιστολόγιο</a><a>Μέντιουμ Αστρολόγοι</a><a>Αγορά Χρόνου Ομιλίας</a></nav>
  <h1 class="hero-title">Τα ζώδια για σήμερα Πέμπτη 17/11</h1>
  <p class="hero-text">Τα ζώδια για σήμερα 17/11 Κριός θα νιώσετε έντονη την ανάγκη να αποσυρθείτε από τις συναναστροφές και να παραμείνετε</p>
  <div class="call-btn"><span class="ico"><svg width="22" height="22" viewBox="0 0 24 24"><path fill="#6B429C" d="M6.6 10.8a15 15 0 0 0 6.6 6.6l2.2-2.2a1 1 0 0 1 1-.25 11.4 11.4 0 0 0 3.6.57 1 1 0 0 1 1 1V20a1 1 0 0 1-1 1A17 17 0 0 1 3 4a1 1 0 0 1 1-1h3.5a1 1 0 0 1 1 1c0 1.25.2 2.45.57 3.57a1 1 0 0 1-.25 1z"/></svg></span>Κλήση</div>
  <div class="wheel" role="img" aria-label="Τροχός ζωδίων σε φωτεινό έναστρο φόντο"></div>
  <div class="thumbs"><span role="img" aria-label="Μικρογραφία ζωδιακού τροχού"></span><span role="img" aria-label="Μικρογραφία φωτογραφίας"></span><span role="img" aria-label="Μικρογραφία φωτογραφίας"></span></div>
  <div class="dots"><i></i><i></i><i></i></div>
</header>

<div class="filters"><span class="on">Αλλά όπως παρατηρ</span><span>Αλλά όπως παρατηρ</span><span>Αλλά όπως παρατηρ</span><span>Αλλά όπως παρατηρ</span><span>Αλλά όπως παρατηρ</span><span>Αλλά όπως παρατηρ</span></div>

<h2 class="section-title" style="left:111px;top:858px">Τελευταίο Ιστολόγιο</h2>
<h2 class="section-title" style="left:786px;top:858px">Πρόσφατα Άρθρα</h2>

<article class="post" style="left:111px;top:946px"><div class="img" role="img" aria-label="Χέρια που απλώνουν κάρτες ταρώ" style="background:linear-gradient(135deg,#c9b9a3,#8a6f55)"></div><div class="meta">11 ώρες πριν</div><h3>Τα ζώδια για σήμερα Παρασκευή 18/11</h3></article>
<article class="post" style="left:440px;top:946px"><div class="img" role="img" aria-label="Ανοιχτό βιβλίο με ζωδιακά σύμβολα" style="background:linear-gradient(135deg,#2f4a52,#b59256)"></div><div class="meta">16 ώρες πριν</div><h3>Ταρώ για σήμερα Πέμπτη 17/11</h3></article>
<article class="post" style="left:111px;top:1293px"><div class="img" role="img" aria-label="Φωτεινός ζωδιακός κύκλος πάνω από βιβλία" style="background:radial-gradient(circle,#f7c46a,#5a4a8a 60%,#2d2b4a)"></div><div class="meta">1 ημέρα πριν</div><h3>Τα ζώδια για σήμερα Πέμπτη</h3></article>
<article class="post" style="left:440px;top:1293px"><div class="img" role="img" aria-label="Ζάρια πάνω σε αστρολογικό χάρτη" style="background:linear-gradient(135deg,#2b3f7a,#5a73b8)"></div><div class="meta">2 ημέρες πριν</div><h3>Ταρώ για σήμερα Τετάρτη 16/11</h3></article>

<ul class="recent">
  <li><div class="img" role="img" aria-label="Ζωδιακός κύκλος" style="background:linear-gradient(135deg,#3a2f8a,#a46ad0)"></div><div><h4>Τα ζώδια για σήμερα Παρασκευή 18/11</h4><div class="time"><svg width="13" height="13" viewBox="0 0 16 16"><circle cx="8" cy="8" r="6.5" fill="none" stroke="#6B429C" stroke-width="1.5"/><path d="M8 4v4l3 2" fill="none" stroke="#6B429C" stroke-width="1.5"/></svg>11 ώρες πριν</div></div></li>
  <li><div class="img" role="img" aria-label="Φωτεινή σφαίρα με σύμβολα" style="background:radial-gradient(circle,#f7d36a,#6a8a3a)"></div><div><h4>Ταρώ για σήμερα Πέμπτη 17/11</h4><div class="time"><svg width="13" height="13" viewBox="0 0 16 16"><circle cx="8" cy="8" r="6.5" fill="none" stroke="#6B429C" stroke-width="1.5"/><path d="M8 4v4l3 2" fill="none" stroke="#6B429C" stroke-width="1.5"/></svg>16 ώρες πριν</div></div></li>
  <li><div class="img" role="img" aria-label="Γυάλινη σφαίρα στο σκοτάδι" style="background:radial-gradient(circle,#a47ad8,#1b1f4a)"></div><div><h4>Τα ζώδια για σήμερα Πέμπτη 17/11</h4><div class="time"><svg width="13" height="13" viewBox="0 0 16 16"><circle cx="8" cy="8" r="6.5" fill="none" stroke="#6B429C" stroke-width="1.5"/><path d="M8 4v4l3 2" fill="none" stroke="#6B429C" stroke-width="1.5"/></svg>1 ημέρα πριν</div></div></li>
  <li><div class="img" role="img" aria-label="Κάρτες ταρώ σε τραπέζι" style="background:linear-gradient(135deg,#4a3a2a,#b08a5a)"></div><div><h4>Ταρώ για σήμερα Τετάρτη 16/11</h4><div class="time"><svg width="13" height="13" viewBox="0 0 16 16"><circle cx="8" cy="8" r="6.5" fill="none" stroke="#6B429C" stroke-width="1.5"/><path d="M8 4v4l3 2" fill="none" stroke="#6B429C" stroke-width="1.5"/></svg>2 ημέρες πριν</div></div></li>
  <li><div class="img" role="img" aria-label="Χέρια με κάρτα ταρώ" style="background:linear-gradient(135deg,#2f3f2f,#8a7a5a)"></div><div><h4>Τα ζώδια για σήμερα Πέμπτη 17/11</h4><div class="time"><svg width="13" height="13" viewBox="0 0 16 16"><circle cx="8" cy="8" r="6.5" fill="none" stroke="#6B429C" stroke-width="1.5"/><path d="M8 4v4l3 2" fill="none" stroke="#6B429C" stroke-width="1.5"/></svg>1 ημέρα πριν</div></div></li>
  <li><div class="img" role="img" aria-label="Ζυγαριά σε μπλε φόντο" style="background:linear-gradient(135deg,#2a6ab8,#e3c24a)"></div><div><h4>Ταρώ για σήμερα Τετάρτη 16/11</h4><div class="time"><svg width="13" height="13" viewBox="0 0 16 16"><circle cx="8" cy="8" r="6.5" fill="none" stroke="#6B429C" stroke-width="1.5"/><path d="M8 4v4l3 2" fill="none" stroke="#6B429C" stroke-width="1.5"/></svg>2 ημέρες πριν</div></div></li>
</ul>

<section class="astro">
  <h2 class="section-title center">Οι αστρολόγοι μας</h2>

  <div class="card" style="left:111px;top:132px"><div class="img" role="img" aria-label="Γυναίκα με ανοιχτά χέρια στο ηλιοβασίλεμα" style="background:linear-gradient(180deg,#f6b46a,#e0743a)"></div><div class="band"><span class="ico"><svg width="18" height="18" viewBox="0 0 24 24"><path fill="#fff" d="M6.6 10.8a15 15 0 0 0 6.6 6.6l2.2-2.2a1 1 0 0 1 1-.25 11.4 11.4 0 0 0 3.6.57 1 1 0 0 1 1 1V20a1 1 0 0 1-1 1A17 17 0 0 1 3 4a1 1 0 0 1 1-1h3.5a1 1 0 0 1 1 1c0 1.25.2 2.45.57 3.57a1 1 0 0 1-.25 1z"/></svg></span><div class="num"><small>Κάλεσε τώρα</small><b>14977</b></div><div class="name">Lena Kostaki</div></div><p>Αλλά για να δείτε από πού προέρχεται όλο αυτό το γεννημένο λάθος όσων κατηγορούν την ευχαρίστηση και υμνούν τον πόνο, θα ανοίξω το όλο θέμα και θα σας εξηγήσω τα ίδια αυτά που από</p></div>
  <div class="card" style="left:443px;top:132px"><div class="img" role="img" aria-label="Χαμογελαστή γυναίκα με πράσινη μπλούζα" style="background:linear-gradient(180deg,#e8dcc8,#3a9a4a)"></div><div class="band"><span class="ico"><svg width="18" height="18" viewBox="0 0 24 24"><path fill="#fff" d="M6.6 10.8a15 15 0 0 0 6.6 6.6l2.2-2.2a1 1 0 0 1 1-.25 11.4 11.4 0 0 0 3.6.57 1 1 0 0 1 1 1V20a1 1 0 0 1-1 1A17 17 0 0 1 3 4a1 1 0 0 1 1-1h3.5a1 1 0 0 1 1 1c0 1.25.2 2.45.57 3.57a1 1 0 0 1-.25 1z"/></svg></span><div class="num"><small>Κάλεσε τώρα</small><b>14977</b></div><div class="name">Thalia</div></div><p>Αλλά για να δείτε από πού προέρχεται όλο αυτό το γεννημένο λάθος όσων κατηγορούν την ευχαρίστηση και υμνούν τον πόνο, θα ανοίξω το όλο θέμα και θα σας εξηγήσω τα ίδια αυτά που από</p></div>
  <div class="card" style="left:773px;top:132px"><div class="img" role="img" aria-label="Χαμογελαστή γυναίκα σε εξωτερικό χώρο" style="background:linear-gradient(180deg,#f2e6d6,#c9a57a)"></div><div class="band"><span class="ico"><svg width="18" height="18" viewBox="0 0 24 24"><path fill="#fff" d="M6.6 10.8a15 15 0 0 0 6.6 6.6l2.2-2.2a1 1 0 0 1 1-.25 11.4 11.4 0 0 0 3.6.57 1 1 0 0 1 1 1V20a1 1 0 0 1-1 1A17 17 0 0 1 3 4a1 1 0 0 1 1-1h3.5a1 1 0 0 1 1 1c0 1.25.2 2.45.57 3.57a1 1 0 0 1-.25 1z"/></svg></span><div class="num"><small>Κάλεσε τώρα</small><b>14977</b></div><div class="name">Ismene</div></div><p>Αλλά για να δείτε από πού προέρχεται όλο αυτό το γεννημένο λάθος όσων κατηγορούν την ευχαρίστηση και υμνούν τον πόνο, θα ανοίξω το όλο θέμα και θα σας εξηγήσω τα ίδια αυτά που από</p></div>

  <div class="card" style="left:111px;top:648px"><div class="img" role="img" aria-label="Γυναίκα ανάμεσα σε φθινοπωρινά φύλλα" style="background:linear-gradient(180deg,#e0a03a,#b83a2a)"></div><div class="band"><span class="ico"><svg width="18" height="18" viewBox="0 0 24 24"><path fill="#fff" d="M6.6 10.8a15 15 0 0 0 6.6 6.6l2.2-2.2a1 1 0 0 1 1-.25 11.4 11.4 0 0 0 3.6.57 1 1 0 0 1 1 1V20a1 1 0 0 1-1 1A17 17 0 0 1 3 4a1 1 0 0 1 1-1h3.5a1 1 0 0 1 1 1c0 1.25.2 2.45.57 3.57a1 1 0 0 1-.25 1z"/></svg></span><div class="num"><small>Κάλεσε τώρα</small><b>14977</b></div><div class="name">Dora Melidou</div></div><p>Αλλά για να δείτε από πού προέρχεται όλο αυτό το γεννημένο λάθος όσων κατηγορούν την ευχαρίστηση και υμνούν τον πόνο, θα ανοίξω το όλο θέμα και θα σας εξηγήσω τα ίδια αυτά που από</p></div>
  <div class="card" style="left:443px;top:648px"><div class="img" role="img" aria-label="Γυναίκα σε δάσος με φως ήλιου" style="background:linear-gradient(180deg,#9ab04a,#4a5a2a)"></div><div class="band"><span class="ico"><svg width="18" height="18" viewBox="0 0 24 24"><path fill="#fff" d="M6.6 10.8a15 15 0 0 0 6.6 6.6l2.2-2.2a1 1 0 0 1 1-.25 11.4 11.4 0 0 0 3.6.57 1 1 0 0 1 1 1V20a1 1 0 0 1-1 1A17 17 0 0 1 3 4a1 1 0 0 1 1-1h3.5a1 1 0 0 1 1 1c0 1.25.2 2.45.57 3.57a1 1 0 0 1-.25 1z"/></svg></span><div class="num"><small>Κάλεσε τώρα</small><b>14977</b></div><div class="name">Selina</div></div><p>Αλλά για να δείτε από πού προέρχεται όλο αυτό το γεννημένο λάθος όσων κατηγορούν την ευχαρίστηση και υμνούν τον πόνο, θα ανοίξω το όλο θέμα και θα σας εξηγήσω τα ίδια αυτά που από</p></div>
  <div class="card" style="left:773px;top:648px"><div class="img" role="img" aria-label="Γυναίκα με γυαλιά σε γραφείο" style="background:linear-gradient(180deg,#5a6a6a,#b8b0a0)"></div><div class="band"><span class="ico"><svg width="18" height="18" viewBox="0 0 24 24"><path fill="#fff" d="M6.6 10.8a15 15 0 0 0 6.6 6.6l2.2-2.2a1 1 0 0 1 1-.25 11.4 11.4 0 0 0 3.6.57 1 1 0 0 1 1 1V20a1 1 0 0 1-1 1A17 17 0 0 1 3 4a1 1 0 0 1 1-1h3.5a1 1 0 0 1 1 1c0 1.25.2 2.45.57 3.57a1 1 0 0 1-.25 1z"/></svg></span><div class="num"><small>Κάλεσε τώρα</small><b>14977</b></div><div class="name">Margot</div></div><p>Αλλά για να δείτε από πού προέρχεται όλο αυτό το γεννημένο λάθος όσων κατηγορούν την ευχαρίστηση και υμνούν τον πόνο, θα ανοίξω το όλο θέμα και θα σας εξηγήσω τα ίδια αυτά που από</p></div>

  <div class="outline-btn" style="left:509px;top:1163px">Δείτε περισσότερα</div>
</section>

<h2 class="section-title center" style="left:0;width:1200px;text-align:center;top:3012px">προσφορές πακέτων</h2>

<div class="pack" style="left:130px;top:3158px;width:315px;height:381px;padding-top:40px"><div class="label">30’ομιλίας</div><div class="price">25€</div><hr><p>Πληρωμή με χρεωστική / πιστωτική κάρτα μέσω PAYRAΠληρωμή με μετα στους παρακάτω λογαριασμούς</p></div>
<div class="pack featured" style="left:443px;top:3115px;width:314px;height:475px;padding-top:83px"><div class="label">60’ομιλίας</div><div class="price">50€</div><hr><p>Πληρωμή με χρεωστική / πιστωτική κάρτα μέσω PAYRAΠληρωμή με μετα στους παρακάτω λογαριασμούς Πληρώνεις τα χρήματα του πακέτου ομιλίας που επέλεξες</p></div>
<div class="pack" style="left:755px;top:3158px;width:315px;height:381px;padding-top:40px"><div class="label">120’ομιλίας</div><div class="price">75€</div><hr><p>Πληρωμή με χρεωστική / πιστωτική κάρτα μέσω PAYRAΠληρωμή με μετα στους παρακάτω λογαριασμούς</p></div>

<div class="solid-btn" style="left:509px;top:3633px">Μάθε περισσότερα</div>

<footer class="site-footer">
  <div class="brand">velorimo<span class="dot"></span></div>
  <nav class="foot-nav"><span>Ιστολόγιο</span><span>|</span><span>Μέντιουμ Αστρολόγοι</span><span>|</span><span>Αγορά Χρόνου Ομιλίας</span></nav>
  <div class="social"><i></i><i></i><i></i><i></i><i></i></div>
  <p class="copy">©2022 Velorimo.All rights reserved.</p>
</footer>

</body>
</html>
```